Custom unique Stationary design for Logistics company

We need a custom, unique , elegant and luxurious full stationary design using our new logo, following these guidelines:
1- Business card: double sided, both sides uses the navy blue as the background main color (same as the code of the navy blue used in our logo).
2- envelope and folder: also use the same navy blue as the main background color.
3- book cover( notepad cover) : same thing with the navy blue
4- letterhead: feel free to use the combination of the colors in our logo.
5- rest of the items are up to your creativity

Target Market(s)

corporates and other businesses

Industry/Entity Type

Logistics and heavy machines contractors

Requirements
Must have
• Letterhead, business card, envelope, notepad cover, paper, file
Nice to have
• navy blue to be main background color for business card, envelope, notepad cover

```html
<!DOCTYPE html>
<html lang="en">
<head>
<meta charset="utf-8">
<title>Meridian Freight Group — Business Card</title>
<link href="https://fonts.googleapis.com/css2?family=Questrial&display=swap" rel="stylesheet">
<style>
  :root {
    --navy: #014f78;
    --orange: #e8582a;
    --white: #ffffff;
    --muted: #c9d3da;
    --stage: #9b9b9b;
  }
  * { box-sizing: border-box; margin: 0; padding: 0; }
  html, body { width: 1200px; height: 1200px; overflow: hidden; }
  body { background: var(--stage); font-family: "Questrial", sans-serif; }
  .canvas { position: relative; width: 1200px; height: 1200px; }

  .card {
    position: absolute; left: 263px; width: 684px; height: 391px;
    background: var(--navy); border-radius: 20px; overflow: hidden; color: var(--white);
  }
  .card--front { top: 165px; }
  .card--back { top: 653px; }

  /* front */
  .brand { position: absolute; left: 40px; top: 140px; width: 290px; text-align: center; }
  .brand__initials { font-size: 94px; line-height: 1; letter-spacing: 2px; color: var(--white); }
  .brand__name { margin-top: 8px; font-size: 11px; letter-spacing: 0.6px; color: var(--muted); white-space: nowrap; }

  .divider { position: absolute; left: 323px; top: 92px; width: 1px; height: 184px; background: rgba(232,88,42,0.55); }

  .contact { position: absolute; left: 350px; top: 104px; white-space: nowrap; }
  .contact__name { font-size: 26px; color: var(--orange); letter-spacing: 0.3px; line-height: 1; }
  .contact__title { margin-top: 8px; font-size: 15px; line-height: 1; }
  .contact__address { margin-top: 14px; font-size: 16px; line-height: 19px; }
  .contact__lines { margin-top: 7px; list-style: none; }
  .contact__lines li { display: flex; align-items: center; height: 20px; font-size: 16px; }
  .contact__lines li.email { font-size: 15px; }
  .contact__lines svg { width: 12px; height: 12px; margin-right: 9px; flex: none; }

  .web-band { position: absolute; left: 0; top: 331px; width: 646px; height: 30px; }
  .web-band__url {
    position: absolute; left: 0; top: 0; width: 615px; height: 30px; line-height: 30px;
    text-align: center; font-size: 15px; letter-spacing: 3.2px; color: var(--navy);
    padding-left: 30px; white-space: nowrap;
  }

  /* back */
  .back-brand { position: absolute; left: 0; top: 32px; width: 100%; text-align: center; font-size: 132px; line-height: 1; letter-spacing: 5px; }
  .back-url { position: absolute; left: 0; top: 173px; width: 100%; text-align: center; font-size: 15px; letter-spacing: 3.4px; white-space: nowrap; }
  .back-glow {
    position: absolute; left: 0; top: 238px; width: 100%; height: 153px;
    background: radial-gradient(ellipse 75% 100% at 45% 100%, rgba(18,230,245,0.55), rgba(0,120,200,0.25) 55%, rgba(1,79,120,0) 80%);
  }
</style>
</head>
<body>
<main class="canvas">

  <section class="card card--front" aria-label="Business card front">
    <div class="brand">
      <div class="brand__initials">MFG</div>
      <div class="brand__name">MERIDIAN FREIGHT GROUP</div>
    </div>

    <div class="divider"></div>

    <div class="contact">
      <p class="contact__name">DANIEL REYES</p>
      <p class="contact__title">President</p>
      <p class="contact__address">1420 Harbor View Road<br>Kenai, Alaska 99611</p>
      <ul class="contact__lines">
        <li>
          <svg viewBox="0 0 12 12"><path d="M2.5 0.8 L4.5 3 L3.4 4.4 Q4.5 6.8 7.6 8.6 L9 7.5 L11.2 9.5 L9.8 11.2 Q4 10.5 0.8 2.2 Z" fill="var(--orange)"/></svg>
          555-238-4170
        </li>
        <li>
          <svg viewBox="0 0 12 12"><rect x="3" y="0.5" width="6" height="11" rx="1" fill="none" stroke="var(--orange)" stroke-width="1.3"/><rect x="5" y="9.3" width="2" height="1" fill="var(--orange)"/></svg>
          555-604-9132
        </li>
        <li class="email">
          <svg viewBox="0 0 12 12"><rect x="0.5" y="2.5" width="11" height="7.5" fill="var(--orange)"/><path d="M0.8 3 L6 7 L11.2 3" fill="none" stroke="var(--navy)" stroke-width="1"/></svg>
          hello@meridianfreightgroup.com
        </li>
      </ul>
    </div>

    <div class="web-band">
      <svg width="646" height="30" viewBox="0 0 646 30" style="position:absolute;left:0;top:0">
        <path d="M0 0 H612 L628 15 L612 30 H0 Z" fill="var(--white)"/>
        <path d="M620 0 H632 L646 15 L632 30 H620 L634 15 Z" fill="var(--orange)"/>
      </svg>
      <div class="web-band__url">www.meridianfreightgroup.com</div>
    </div>
  </section>

  <section class="card card--back" aria-label="Business card back">
    <div class="back-brand">MFG</div>
    <div class="back-url">meridianfreightgroup.com</div>
    <div class="back-glow" role="img" aria-label="Large decorative brand sweep in cyan and blue tones"></div>
  </section>

</main>
</body>
</html>
```